Briloran Clear Springs needs a new business card design (we produce and sell pure bottled water)

We need a clean modern design for our new business cards, We have an existing logo which ultimately cannot be changed, however it could be slighty improved and the colours adjusted. We have this existing logo on all of our bottles, vehicles etc.

Our company slogan is "Clear right to the final sip".
Along with our relevant company information
(Address, phone, website email etc) we will only be using names and not putting position titles for flexibilty.

We are looking for a clean, minimalist modern design.

You can view our website (if need of an update also!) to see our business.

Industry/Entity Type

Business

Contact Information for Business Card

Staff Name : XXXXXX XXXXXX
Address : 9/41 Tavenor St
Halden Rise QLD 4172
Staff Mobile Number : 04XX XXX XXX
Office Phone Number : 07 3918 2457
Staff Email Address : XXXX@brilorancleargo.com.au
Website : www.brilorancleargo.com.au

Font styles to use
Sans Serif

Colors
cee9f5
33a6d7
0492cd
0455a3
3276b5
85abd2
cedeed

Requirements
Must have
• The ability to edit and change the staff members details as we will need to edit for each respective staff member (7 in total)

```html
<!DOCTYPE html>
<html lang="en">
<head>
<meta charset="utf-8">
<title>Briloran Clear Springs – Business Card</title>
<link href="https://fonts.googleapis.com/css2?family=Open+Sans:wght@400;600;700;800&display=swap" rel="stylesheet">
<style>
  :root {
    --navy: #14118f;
    --navy-faint: #2a28a0;
    --ink: #1a1a1a;
    --rule: #d4d6de;
    --paper: #ffffff;
    --stage: #e9ebef;
    --bottle-light: #cee9f5;
    --bottle-mid: #85abd2;
    --bottle-dark: #3276b5;
  }
  * { box-sizing: border-box; margin: 0; padding: 0; }
  html, body {
    width: 1200px; height: 864px; overflow: hidden;
    background: var(--stage);
    font-family: "Open Sans", Arial, sans-serif;
  }
  .sheet {
    position: relative; width: 1200px; height: 864px;
    display: flex; flex-direction: column; align-items: center; justify-content: center; gap: 50px;
  }
  .card {
    position: relative; width: 560px; height: 342px;
    box-shadow: 0 6px 18px rgba(0,0,0,.14);
  }
  .card-back { background: var(--navy); }
  .back-name {
    position: absolute; left: 0; right: 0; top: 50%; transform: translateY(-50%);
    text-align: center; color: var(--navy-faint);
    font-weight: 800; font-size: 34px; letter-spacing: .5px;
  }
  .card-front { background: var(--paper); color: var(--ink); }
  .product-photo {
    position: absolute; left: 34px; top: 26px; width: 80px; height: 100px;
    border-radius: 16px 16px 12px 12px;
    background: linear-gradient(135deg, var(--bottle-light), var(--bottle-mid) 55%, var(--bottle-dark));
  }
  .staff-name {
    position: absolute; left: 38px; top: 162px;
    color: var(--navy); font-weight: 700; font-size: 19px;
  }
  .rule { position: absolute; height: 1px; background: var(--rule); }
  .rule-name { left: 20px; top: 200px; width: 520px; }
  .rule-contact { left: 300px; top: 262px; width: 240px; }
  .address {
    position: absolute; left: 38px; top: 210px;
    font-size: 13.5px; line-height: 19px;
  }
  .brand {
    position: absolute; right: 38px; top: 146px; text-align: right;
  }
  .brand-name {
    color: var(--navy); font-weight: 800; font-size: 22px; line-height: 1.1;
  }
  .slogan { margin-top: 6px; font-size: 14.5px; color: var(--ink); }
  .contacts {
    position: absolute; right: 28px; top: 272px; list-style: none;
    font-size: 13.5px; line-height: 19px; text-align: right;
  }
  .contacts li { display: flex; align-items: center; justify-content: flex-end; gap: 10px; }
  .contacts svg { width: 11px; height: 11px; fill: var(--navy); flex: none; }
</style>
</head>
<body>
<main class="sheet">
  <section class="card card-back" aria-label="Card back">
    <div class="back-name">Briloran Clear Springs</div>
  </section>

  <section class="card card-front" aria-label="Card front">
    <div class="product-photo" role="img" aria-label="Photo of a large bottled water jug"></div>

    <h1 class="staff-name">Marcus Delveen</h1>
    <div class="rule rule-name"></div>
    <p class="address">9/41 Tavenor St<br>Halden Rise QLD 4172</p>

    <div class="brand">
      <div class="brand-name">Briloran Clear Springs</div>
      <p class="slogan">Clear right to the final sip</p>
    </div>

    <div class="rule rule-contact"></div>
    <ul class="contacts">
      <li>0400 517 238
        <svg viewBox="0 0 12 12" aria-hidden="true"><path d="M3 0h6a1 1 0 0 1 1 1v10a1 1 0 0 1-1 1H3a1 1 0 0 1-1-1V1a1 1 0 0 1 1-1zm0 2v7h6V2zm3 8.2a.7.7 0 1 0 0 .01z"/></svg>
      </li>
      <li>07 3918 2457
        <svg viewBox="0 0 12 12" aria-hidden="true"><path d="M2.4 0.6l1.8 2.2-1 1.2c.7 1.6 1.9 2.8 3.6 3.6l1.2-1 2.2 1.8-.8 2.2C5 10.4 1.6 7 .2 1.4z"/></svg>
      </li>
      <li>info@brilorancleargo.com.au
        <svg viewBox="0 0 12 12" aria-hidden="true"><path d="M0 2h12v1L6 7 0 3zm0 2.2l6 4 6-4V10H0z"/></svg>
      </li>
    </ul>
  </section>
</main>
</body>
</html>
```